Ngọc Sáng Đường Về (The Lantern Of Dawn Of Quiet Rivers)

The purpose of this project is to share the Velra Orin technique of Spiritual Meditation. The technique is originally in the Vietnamese language and need to share worldwide in other languages.

Spiritual Meditation through Vela Orin meditation method to assist mind traveling through body to eternity. This method of meditation has many techniques and different purpose of all levels of understanding of mind, the more understanding the more explored the ability self esteem, self conscious, self determination to search for eternity. It’s not all could practice, it’s depending the previous life’s experiences that’s existing in their own mind. Because when a human life was born that never know their mind history came from. All human life has been programmed by almighty gods or the gods of living universe.

Heaven, Earth, Human were all connected through minds not though the body, the body could not reach to heaven.

Only mind could reach to Heaven because almighty gods design them. All life’s on earth are controlled by almighty though mind.

***UPDATED GUIDE FOR DESIGNERS:

1/. Theme page: I wish to have my own theme as a background to be supplied [p1: Theme]
(a) Use the logo provided [p2] and add the words on the bottom "Thiên Địa Nhân" If the designers
are foreign languages then they use alphabetical characters throughout the design.
(b). In the existing site (lanvy.org) has a picture [p3] of the author of the book which has 4 words
"Ngọc Sáng Đường Về" I want to have it on my theme page in a similar dimension.
(c). I like to add a picture [p4] of a white flower on the right-hand side of the theme to balance with
the right side.
(d) At the bottom of the theme
(i) Write the words "Welcome To lanvy.org" and the next line down
(ii). Write the words "Tu Thiền Hoàng Mai Thanh Tịnh Cửu Sơn Lạc Viên Đông Nguyên"

2/. Menu:
(a). Introduction: Trang Chủ "Lời Giới Thiệu"
(b). Author story: Tiểu Sử
(c). Books "The Lantern of quiet dawn rivers" Kinh Sách "Ngọc Sáng Đường Về"
(i) Book 1
(ii) Book 2
(iii) Book 3
(iv) Book 4
(v) Book 5
(vi) Book 6 to be continued..
(d). Method for beginners: Phương pháp Thiền cho 6 tháng đầu cho hành giả mới tham gia
(e) Method for Practitioners: Thiền Thực Hành Theo Hoàng Mai Thanh Tịnh Cửu Sơn Lạc Viên Đông
Nguyên
(f) Register/Login: Đăng nhập
(g). Contact: Liên hệ

The following is my attached content to support the information

Target Market(s)

Body and Mind

Industry/Entity Type

Spiritual Meditaion

Coding

Coded - Design and coding required

Number of Pages Required

5+ page

Font styles to use
Sans Serif

Requirements
Must have
• Clearly presented the author of books and audio
Nice to have
• The author wish to introduce her books which were written through her spiritual meditaion she wish to share to all mankind
Should not have
• Advertise, other religious contain...

```html
<!DOCTYPE html>
<html lang="vi">
<head>
<meta charset="utf-8">
<title>Lan Vy – Thiền</title>
<link href="https://fonts.googleapis.com/css2?family=Poppins:wght@400;500;600;700&family=Lato:wght@400;700&family=Roboto:wght@400;500&display=swap" rel="stylesheet">
<style>
:root{
  --gold:#e1c04c;
  --gold-deep:#d3a92d;
  --gold-light:#eed679;
  --ink:#1d1d1d;
  --text:#555;
  --soft:#f5f5f5;
  --white:#fff;
  --black:#000;
}
*{margin:0;padding:0;box-sizing:border-box}
html,body{width:1200px;height:3925px;overflow:hidden;background:var(--white)}
body{position:relative;font-family:'Lato',sans-serif;color:var(--text)}
.abs{position:absolute}
.btn{position:absolute;background:var(--gold);color:var(--white);font-family:'Poppins',sans-serif;font-weight:600;font-size:15px;display:flex;align-items:center;justify-content:center;text-transform:uppercase;letter-spacing:.3px}
.heading{position:absolute;font-family:'Poppins',sans-serif;font-weight:600;color:var(--ink);text-transform:uppercase;text-align:center}

/* header */
.site-header{position:absolute;left:0;top:0;width:1200px;height:78px;background:var(--white);z-index:5}
.brand{position:absolute;left:111px;top:8px;width:118px;height:108px;border-radius:50%;background:#2f4c8c;border:3px solid #d8d8d8;display:flex;align-items:center;justify-content:center;color:var(--white);font-family:'Poppins',sans-serif;font-weight:600;font-size:20px;z-index:6}
.nav a{position:absolute;top:29px;font-family:'Lato',sans-serif;font-size:15px;color:#444;text-decoration:none}
.lang-dot{position:absolute;left:1006px;top:20px;width:36px;height:36px;border-radius:50%;background:#d72a1e}
.lang{position:absolute;left:1054px;top:28px;font-family:'Poppins',sans-serif;font-weight:600;font-size:15px;color:var(--ink)}

/* hero */
.hero-title{position:absolute;left:110px;top:265px;font-family:'Poppins',sans-serif;font-weight:600;font-size:46px;line-height:64px;color:var(--white);text-transform:uppercase}
.hero-sub{position:absolute;left:111px;top:402px;width:380px;font-size:14px;line-height:26px;color:var(--white)}

/* story */
.story-title{position:absolute;left:563px;top:870px;font-family:'Poppins',sans-serif;font-weight:600;font-size:35px;color:var(--ink)}
.story-text{position:absolute;left:563px;top:925px;width:530px;font-size:14.4px;line-height:30px;color:var(--text)}
.author{position:absolute;left:781px;top:1295px;font-family:'Poppins',sans-serif;font-weight:600;font-size:19px;color:var(--ink)}
.author span{color:var(--gold);font-weight:400}

/* rules */
.rules-sub{position:absolute;left:0;width:1200px;top:1616px;text-align:center;font-family:'Poppins',sans-serif;font-weight:600;font-size:17px;color:var(--ink)}
.rules-text{position:absolute;left:180px;width:840px;top:1656px;text-align:center;font-size:13px;line-height:26px;color:var(--text)}

/* methods */
.method{position:absolute;top:2425px;width:309px;height:371px;display:flex;align-items:flex-end;justify-content:center;padding-bottom:38px;color:var(--white);font-family:'Poppins',sans-serif;font-weight:600;font-size:20px;text-transform:uppercase}

/* books */
.books-text{position:absolute;left:180px;width:840px;top:2950px;text-align:center;font-size:14px;line-height:30px;color:var(--text)}
.book{position:absolute;width:312px;height:172px;background:var(--white);box-shadow:0 2px 14px rgba(0,0,0,.08)}
.book .cover{position:absolute;left:22px;top:22px;width:92px;height:122px;background:linear-gradient(160deg,#f1f1f1 0%,#f1f1f1 45%,#8fc0d6 46%,#4d8db0 100%);box-shadow:2px 3px 6px rgba(0,0,0,.25)}
.book h3{position:absolute;left:142px;top:22px;width:150px;font-family:'Roboto',sans-serif;font-weight:500;font-size:21px;line-height:25px;color:#555}
.book .more{position:absolute;left:142px;width:132px;height:38px;background:var(--gold);color:var(--white);font-family:'Roboto',sans-serif;font-weight:500;font-size:14px;display:flex;align-items:center;justify-content:center}

/* footer */
.footer-brand{position:absolute;left:168px;top:3630px;width:170px;height:150px;border-radius:50%;background:#2f4c8c;border:3px solid #d8d8d8;display:flex;align-items:center;justify-content:center;color:var(--white);font-family:'Poppins',sans-serif;font-weight:600;font-size:24px}
.footer-col{position:absolute;top:3653px;list-style:none;font-family:'Lato',sans-serif;font-size:13.5px;line-height:26px;color:var(--white)}
.email{position:absolute;left:835px;top:3656px;width:253px;height:36px;background:var(--white);font-size:11px;color:#999;padding:11px 16px}
.subscribe{position:absolute;left:835px;top:3706px;width:99px;height:36px;background:var(--gold);color:var(--white);font-family:'Poppins',sans-serif;font-weight:500;font-size:12px;display:flex;align-items:center;justify-content:center}
.copyright{position:absolute;left:0;width:1200px;top:3844px;text-align:center;font-size:12px;color:var(--white)}
</style>
</head>
<body>

<header class="site-header">
  <nav class="nav">
    <a style="left:435px">Trang chủ</a>
    <a style="left:542px">Về chúng tôi</a>
    <a style="left:667px">Thiền</a>
    <a style="left:746px">Sách</a>
    <a style="left:819px">Liên hệ chúng tôi</a>
  </nav>
  <div class="lang-dot"></div>
  <div class="lang">VE ⌄</div>
</header>
<div class="brand">Lan Vy</div>

<!-- hero -->
<svg class="abs" style="left:0;top:78px" width="1200" height="720" viewBox="0 0 1200 720">
  <defs>
    <linearGradient id="heroFill" x1="0" y1="0" x2="1" y2="1">
      <stop offset="0" stop-color="#e9b98a"/>
      <stop offset="0.45" stop-color="#a0705a"/>
      <stop offset="1" stop-color="#4d3a36"/>
    </linearGradient>
  </defs>
  <rect width="1200" height="720" fill="var(--soft)"/>
  <path d="M0 0H1200V615C1050 690 820 722 600 720C380 718 180 680 0 612Z" fill="var(--gold)"/>
  <path d="M0 0H1200V590C1040 670 820 704 600 702C380 700 180 662 0 600Z" fill="url(#heroFill)" role="img" aria-label="Ảnh người phụ nữ ngồi thiền bên hồ nước lúc hoàng hôn, núi phía sau"/>
</svg>
<div class="hero-title">Chào mừng<br>bạn đến Lan Vy</div>
<div class="hero-sub">Giặc giã nổi lên, gia đình cha mẹ tôi và một số bạn bè<br>phải di tản đến tá túc</div>
<div class="btn" style="left:111px;top:474px;width:175px;height:50px">Bắt đầu</div>

<!-- story -->
<svg class="abs" style="left:0;top:798px" width="1200" height="650" viewBox="0 0 1200 650">
  <path d="M0 565C200 630 400 650 600 650C800 650 1000 630 1200 565V0H0Z" fill="var(--soft)"/>
</svg>
<div class="abs" role="img" aria-label="Ảnh người phụ nữ ngồi thiền ngoài trời" style="left:94px;top:889px;width:421px;height:421px;border-radius:50%;background:radial-gradient(circle at 50% 55%,#e8e2d8 0%,#9c9a6e 55%,#5d6b4a 100%)"></div>
<div class="story-title">CÂU CHUYỆN</div>
<div class="story-text">
Tôi tên là Trần Thị Lan Vy.<br>
Sanh ngày: 03/09/1950 tại làng Phước Hòa – Quận Bình Sơn, Tỉnh An Điền.<br>
Cha là: Trần Văn Phúc – Chết năm 88 tuổi.<br>
Mẹ là: Ngô Thị Lựu – Chết năm 84 tuổi.<br>
Sống trong gia đình đông con ( 5 anh, 1 chị gái). Khi tôi lớn lên nghe mẹ kể<br>lại là : sanh tôi ra trong lúc chiến tranh, gia đình phải chạy giặc.<br>
Quê ở tận làng Phước Hòa ( Rạch Đông), muốn lên tỉnh phải đi bằng tàu, không<br>có đường xe. Lúc chạy giặc thì mẹ có mang sắp đẻ, bầu thai đó là tôi.<br>
Giặc giã nổi lên, gia đình cha mẹ tôi và một số bạn bè phải di tản đến tá túc<br>với một người bạn của cha mẹ tôi. Nhà người bạn tương đối rộng và cất<br>chắc chắn (để tránh bom đạn). Tôi cất tiếng khóc chào đời trong cơn loạn lạc.
</div>
<div class="btn" style="left:567px;top:1281px;width:184px;height:53px">Tìm hiểu thêm</div>
<div class="author">Tác giả: <span>Tran Thi Lan Vy.</span></div>

<!-- rules -->
<div class="heading" style="left:0;width:1200px;top:1556px;font-size:34px">Luật vận chuyển</div>
<div class="rules-sub">Sau khi xem xét nội tâm linh hồn, hãy tiếp tục tập Pháp Luân Thường Chuyển như sau:</div>
<div class="rules-text">Vẫn ở tư thế ngồi, từ từ hạ hai cánh tay xuống hai bên, lòng bàn tay úp xuống đùi. Đầu thẳng, cằm thu vào, lưỡi thu vào, răng kề răng,<br>nhắm mắt, trong tâm nhìn thẳng từ giữa lông mày ra phía trước, tập trung ở đỉnh đầu. Thở ra và hít vào bằng mũi, thở nhịp nhàng, liên tục,<br>không ngã Thở ra và hít vào bằng mũi, thở nhịp nhàng, liên tục, không ngã</div>
<div class="btn" style="left:507px;top:1752px;width:186px;height:54px">Tìm hiểu thêm</div>

<!-- gold band -->
<svg class="abs" style="left:0;top:1960px" width="1200" height="880" viewBox="0 0 1200 880">
  <defs>
    <radialGradient id="band" cx="0.5" cy="0.35" r="0.6">
      <stop offset="0" stop-color="var(--gold-light)"/>
      <stop offset="1" stop-color="var(--gold-deep)"/>
    </radialGradient>
  </defs>
  <path d="M0 115C200 40 400 20 600 20C800 20 1000 40 1200 115V645C1000 740 800 800 600 800C400 800 200 740 0 645Z" fill="url(#band)"/>
</svg>
<div class="abs" role="img" aria-label="Ảnh người ngồi thiền trên tảng đá giữa biển mây và núi" style="left:157px;top:1855px;width:886px;height:364px;background:linear-gradient(180deg,#6c8a89 0%,#7f9a97 45%,#d9dedd 70%,#9c8670 100%)"></div>
<div class="heading" style="left:0;width:1200px;top:2298px;font-size:35px;line-height:49px;color:#1d1d1d">Phương pháp thiền theo<br>Hoàng Mai Thanh Tịnh</div>

<div class="method" role="img" aria-label="Ảnh bàn tay hướng lên trời lúc hoàng hôn" style="left:111px;background:linear-gradient(180deg,#c98a1e 0%,#8a5212 60%,#2a1608 100%)">Người cầu nguyện</div>
<div class="method" role="img" aria-label="Ảnh người phụ nữ ngồi nhìn hoàng hôn" style="left:446px;background:linear-gradient(180deg,#eadfc8 0%,#b89266 50%,#3e2c1e 100%)">Thức tỉnh tâm hồn</div>
<div class="method" role="img" aria-label="Ảnh người ngồi thiền trên tảng đá với đàn chim bay" style="left:781px;background:linear-gradient(180deg,#cfc8ba 0%,#c79a62 50%,#4a3220 100%)">Pháp luân thường</div>

<!-- books -->
<div class="heading" style="left:0;width:1200px;top:2890px;font-size:35px">Sách của chúng tôi</div>
<div class="books-text">Bức thư của vị Hiền Nhân luôn viết cho tôi để ngày 8 tháng 4 năm 2001. Đức Thầy dạy rằng “con cần phải lấy một cuốn<br>sổ để ghi lại những gì con đã chứng ngộ, sau này sẽ in thành sách để đời”. Theo hướng dẫn, sau khi thiền xong, tôi nhớ lại<br>những cảm tưởng của mình trong lúc thiền và ghi lại, in thành sách, và xuất bản năm tập.</div>

<div class="book" style="left:111px;top:3070px"><div class="cover" role="img" aria-label="Ảnh bìa sách"></div><h3>Con đường an tịnh giữa đời.</h3><div class="more" style="top:110px">Tìm hiểu thêm</div></div>
<div class="book" style="left:443px;top:3070px"><div class="cover" role="img" aria-label="Ảnh bìa sách"></div><h3>Ánh Sáng Nội Tâm.</h3><div class="more" style="top:110px">Tìm hiểu thêm</div></div>
<div class="book" style="left:775px;top:3070px"><div class="cover" role="img" aria-label="Ảnh bìa sách"></div><h3>Bầu trời trong tâm.</h3><div class="more" style="top:110px">Tìm hiểu thêm</div></div>
<div class="book" style="left:277px;top:3261px"><div class="cover" role="img" aria-label="Ảnh bìa sách"></div><h3>Những trang ghi chép tĩnh lặng (phần 1)</h3><div class="more" style="top:110px">Tìm hiểu thêm</div></div>
<div class="book" style="left:609px;top:3261px"><div class="cover" role="img" aria-label="Ảnh bìa sách"></div><h3>Những trang ghi chép tĩnh lặng (phần 2)</h3><div class="more" style="top:110px">Tìm hiểu thêm</div></div>

<!-- footer -->
<svg class="abs" style="left:0;top:3510px" width="1200" height="415" viewBox="0 0 1200 415">
  <path d="M0 105C200 40 400 8 600 8C800 8 1000 40 1200 105V415H0Z" fill="var(--gold)"/>
  <path d="M0 125C200 60 400 28 600 28C800 28 1000 60 1200 125V415H0Z" fill="var(--black)"/>
</svg>
<div class="footer-brand">Lan Vy</div>
<ul class="footer-col" style="left:437px">
  <li>câu hỏi thường gặp</li><li>Liên hệ chúng tôi</li><li>Chính sách hoàn tiền</li><li>Chính sách bảo mật</li><li>Điều khoản dịch vụ</li>
</ul>
<ul class="footer-col" style="left:652px">
  <li>Trang chủ</li><li>Các sản phẩm</li><li>Về chúng tôi</li><li>Liên hệ chúng tôi</li><li>Blog</li>
</ul>
<div class="email">Địa chỉ email</div>
<div class="subscribe">Đặt mua</div>
<div class="copyright">© 2023 Lanvy | Đã đăng ký Bản quyền | từ chối trách nhiệm</div>

</body>
</html>
```